Kelvor Engineers: Why you should hire us keepsake

New design. Open to plastic cards. We are an engineering firm that designs cell phone towers and commercial buildings. Please check out our website www.kelvorstruct.com for more details. We want people to remember our card and for it to be useful if possible. We want the same look and feel on these cards to be translated to other marketing material we may need such as brochures.

Target Market(s)

Architects, Developers and Telecommunication Carriers

Industry/Entity Type

Engineering

Contact Information for Business Card

Card with our company colors, logo, and innovative design with elements related to our industry.

Font styles to use
Sans Serif

Colors
9bcb3c
abd036
0255a3

Requirements
Must have
• Sleek and hip design
Nice to have
• Bright lime green and navy coloring that pops with an innovative design.
Should not have
• A basic and boring design

```html
<!DOCTYPE html>
<html lang="en">
<head>
<meta charset="utf-8">
<title>Kelvor Engineers Business Card</title>
<link rel="stylesheet" href="https://fonts.googleapis.com/css2?family=Roboto:wght@400;500&family=Roboto+Condensed:wght@500;700&display=swap">
<style>
  :root {
    --backdrop: #1e1e1e;
    --lime: #00f000;
    --navy: #022a5a;
    --paper: #f2f2f2;
    --ink-light: #ffffff;
  }
  html, body {
    margin: 0;
    padding: 0;
    width: 1200px;
    height: 960px;
    overflow: hidden;
    background: var(--backdrop);
  }
  .stage {
    position: relative;
    width: 1200px;
    height: 960px;
  }
  .card {
    position: absolute;
    width: 600px;
    height: 343px;
    overflow: hidden;
  }
  .card--front { left: 314px; top: 113px; background: var(--paper); }
  .card--back  { left: 311px; top: 472px; background: var(--navy); }

  .front-shapes {
    position: absolute;
    inset: 0;
  }
  .wordmark {
    position: absolute;
    font-family: "Roboto Condensed", Arial, sans-serif;
    font-weight: 700;
    color: var(--lime);
    text-transform: uppercase;
    white-space: nowrap;
    margin: 0;
    line-height: 1;
  }
  .wordmark--front {
    right: 74px;
    top: 78px;
    font-size: 38px;
  }
  .holder-name {
    position: absolute;
    left: 34px;
    top: 205px;
    margin: 0;
    font-family: "Roboto Condensed", Arial, sans-serif;
    font-weight: 500;
    font-size: 20px;
    color: var(--ink-light);
    text-transform: uppercase;
    letter-spacing: 0.2px;
  }
  .contact-list {
    position: absolute;
    left: 34px;
    top: 241px;
    margin: 0;
    padding: 0;
    list-style: none;
    font-family: "Roboto", Arial, sans-serif;
    font-size: 14px;
    color: var(--ink-light);
  }
  .contact-list li {
    display: flex;
    align-items: center;
    height: 19px;
  }
  .contact-list svg {
    width: 13px;
    height: 13px;
    margin-right: 10px;
    fill: var(--ink-light);
  }

  .wordmark--back {
    left: 0;
    right: 0;
    top: 128px;
    text-align: center;
    font-size: 48px;
  }
  .tagline {
    position: absolute;
    left: 0;
    right: 0;
    top: 267px;
    display: flex;
    justify-content: center;
    align-items: center;
    gap: 3px;
    margin: 0;
    font-family: "Roboto", Arial, sans-serif;
    font-weight: 500;
    font-size: 15px;
    letter-spacing: 0.3px;
    color: var(--lime);
    text-transform: uppercase;
  }
  .tagline::before, .tagline::after {
    content: "";
    width: 30px;
    height: 2px;
    background: var(--ink-light);
  }
  .locations {
    position: absolute;
    left: 0;
    right: 0;
    top: 288px;
    margin: 0;
    text-align: center;
    font-family: "Roboto", Arial, sans-serif;
    font-size: 15px;
    color: var(--ink-light);
    letter-spacing: 0.7px;
  }
</style>
</head>
<body>
<main class="stage">
  <section class="card card--front" aria-label="Business card front">
    <svg class="front-shapes" width="600" height="343" viewBox="0 0 600 343" aria-hidden="true">
      <polygon points="0,0 91,0 398,343 0,343" fill="var(--lime)"/>
      <polygon points="513,0 600,0 600,97" fill="var(--navy)"/>
    </svg>
    <p class="wordmark wordmark--front">Kelvor Engineers</p>
    <h1 class="holder-name">Dana Whitfield Morrow</h1>
    <ul class="contact-list">
      <li><svg viewBox="0 0 16 16"><path d="M3.5 1l3 3-1.8 1.8c.9 2 2.5 3.6 4.5 4.5L11 8.5l3 3-2 2.5C6.5 13.5 2.5 9.5 1 3.5z"/></svg>555.014.2290</li>
      <li><svg viewBox="0 0 16 16"><path d="M4.5 0h7a1 1 0 0 1 1 1v14a1 1 0 0 1-1 1h-7a1 1 0 0 1-1-1V1a1 1 0 0 1 1-1zm.5 2v10h6V2zm3 11a1 1 0 1 0 0 2 1 1 0 0 0 0-2z"/></svg>555.018.3341</li>
      <li><svg viewBox="0 0 16 16"><path d="M1 3h14v1.5L8 9 1 4.5zM1 6l7 4.5L15 6v7H1z"/></svg>dmorrow@kelvorstruct.com</li>
      <li><svg viewBox="0 0 16 16"><path d="M8 1a7 7 0 1 0 0 14A7 7 0 0 0 8 1zm-1 2.2c-.6 1-1.8 1.3-2 2.5.6.8 1.8.4 2.2 1.4.3.9-.5 1.6 0 2.6.4.8 0 2-.3 2.7A5.3 5.3 0 0 1 3 5c1-.8 2.5-1.7 4-1.8zm2.5.2a5.3 5.3 0 0 1 3.2 6.8c-.6-.5-.8-1.6-1.7-1.8-.9-.2-1.7.3-2.3-.4-.5-.6.2-1.5-.2-2.2-.3-.6-1.2-.5-1.3-1.2 0-.6 1.4-.8 2.3-1.2z"/></svg>www.kelvorstruct.com</li>
    </ul>
  </section>

  <section class="card card--back" aria-label="Business card back">
    <p class="wordmark wordmark--back">Kelvor Engineers</p>
    <p class="tagline">Multi-Discipline Engineering</p>
    <p class="locations">Northvale | Ridgeport | Lakemont | Cedar Bluff</p>
  </section>
</main>
</body>
</html>
```